Snoutsaver.net Dog Coupon Site Website Design

TailThrift - Dog Coupon Site Design Brief

Project Overview
**Site Name:** SnoutSaver.net
**Purpose:** A modern coupon aggregation platform specifically for dog and pet-related products and services
**Target Audience:** Dog owners, pet enthusiasts, budget-conscious pet parents

Brand Identity & Visual Direction

Typography
- **Headers:** Modern sans-serif (Inter or similar) - Clean and friendly
- **Body:** Readable sans-serif with good mobile legibility
- **Accent:** Playful but professional font for coupon codes

Design Principles
- **Flat Design:** Clean, minimal with subtle shadows
- **Friendly & Approachable:** Rounded corners, soft edges
- **Trust-Building:** Clear pricing, transparent savings
- **Scannable:** Easy-to-read coupon codes and offers

## User Experience & Functionality

### Homepage Features
1. **Hero Section**
- Clear value proposition
- Search functionality
- Featured savings highlight

2. **Coupon Cards**
- One-click copy functionality
- Clear discount display
- Store/brand logos
- Expiration dates
- "Get Deal" call-to-action

3. **Navigation**
- Categories (Food, Toys, Health, Services, etc.)
- Popular stores
- Latest deals

### Interactive Elements
- **Copy Button:** Instant feedback when coupon copied
- **Deal Pages:** Detailed offer information, terms, store details
- **Search & Filter:** By category, store, discount amount
- **Mobile Menu:** Hamburger navigation for mobile

## Technical Requirements

### Responsive Design
- **Mobile-First:** Optimized for touch interactions
- **Tablet:** Adapted layout for medium screens
- **Desktop:** Full-width utilization with sidebar potential

### Performance
- **Fast Loading:** Optimized images, minimal JavaScript
- **Accessibility:** WCAG compliant, screen reader friendly
- **SEO Optimized:** Structured data for deals and offers

## Content Strategy

### Deal Categories
- Dog Food & Treats
- Toys & Accessories
- Health & Grooming
- Training & Services
- Outdoor & Travel

### Key Messaging
- "Save on everything your dog loves"
- "Verified deals updated daily"
- "Your pup deserves the best for less"

## Conversion Optimization

### Trust Elements
- Deal verification badges
- User reviews/ratings
- Clear savings calculations
- Expiration date transparency

### Call-to-Actions
- "Copy Code" (primary action)
- "Get Deal" (secondary action)
- "View All [Store] Deals"

## Success Metrics
- Coupon copy rate
- Click-through to retailer
- User return visits
- Mobile vs desktop usage
- Category performance

This design brief ensures a user-friendly, trustworthy platform that makes finding and using pet deals effortless while maintaining a warm, dog-loving community feel.

1. Design Objective
Create a warm, energetic space where dog lovers instantly feel welcomed and confident they’re finding genuine savings for their furry friends. Everything from the layout to the smallest icon should reinforce trust, delight, and simplicity.
2. Visual Personality
Color Palette: Soft, cheerful hues—think warm yellows and gentle blues—that evoke sunshine and playfulness without overwhelming.
Typography:
Headings: A modern, friendly sans‑serif (like Inter) with open letterforms to feel approachable.
Body Copy: Highly legible sans‑serif with generous line spacing for comfort on small screens.
Accent Font: A slightly quirky, hand‑drawn style used sparingly for coupon codes and special call‑outs, giving a personal, “paw‑picked” touch.
Imagery & Icons: Real‑life photographs of happy dogs interspersed with clean line‑icons of bones, paw prints, and hearts. Rounded shapes and subtle shadows keep the look soft and contemporary.
3. Layout & Hierarchy
Hero Area:
Full‑bleed image of a joyful dog, overlaid with a single, punchy tagline (“Save on everything your dog loves”).
Prominent search bar centered to invite exploration.
Offer Grid:
Generous white space around each coupon card so the eye can rest and scan easily.
Coupon cards feature a bold discount label, brand logo, and a friendly “Get Deal” button.
A playful “Copied!” animation briefly replaces the button once the code is grabbed.
Navigation:
A fixed header with clear category labels (Food, Toys, Health, Services).
A secondary “Popular Stores” carousel below to spotlight key partners.
4. Interaction & Motion
Micro‑interactions:
Hover state for cards subtly lifts the card and deepens its shadow, inviting a click.
Copy‑code button pulses once on hover, hinting at its one‑click magic.
Transitions:
Smooth fades between deal filters and search results to reassure users that the site is responding.
Loading indicators shaped like spinning collars or wagging tails to keep the theme consistent.
5. Accessibility & Inclusivity
Ensure all text meets contrast standards so every pet parent—regardless of vision—can read offers with ease.
Interactive elements sized for easy tapping on touchscreens.
Alt‑text for all imagery describing dogs, products, and actions for screen‑reader users.
6. Emotional Tone
From the moment someone lands on SnoutSaver.net, they should feel the joy of treating their dog without guilt. Friendly copy (“Your pup deserves the best for less”) paired with bright visuals will create a sense of community and shared passion.
7. Success by Design
Scan‑ability: Users should spot great deals in under two seconds.
Trust Signals: Badges (“Verified Savings”), clear expiration dates, and reviewer star icons should feel earned and prominent.
Return Visits: A “My Favorite Deals” heart icon encourages saving and returning, reinforced by subtle reminders in the UI.
This design approach keeps dog lovers front and center—making sure every graphic, font choice, and interaction feels like it was lovingly tailored for them.

Target Market(s)

Dog Lovers looking for good deals

Industry/Entity Type

Coupon Code

Number of Pages Required

4 page

Font styles to use
Sans Serif

Requirements
Must have
• Modern look, coupon copy cards it's a deal site and I want the coupon code and copy in the coupon card, blog section, review section, modern footer/header
Nice to have
• Modern coupon code website, easy to use

```html
<!DOCTYPE html>
<html lang="en">
<head>
<meta charset="utf-8">
<title>SnoutSaver – Save on Everything your Dog Loves</title>
<link href="https://fonts.googleapis.com/css2?family=Inter:wght@400;500;600;700&display=swap" rel="stylesheet">
<style>
:root{
  --orange:#f6a623;
  --orange-dark:#e8951a;
  --ink:#2b2b2b;
  --muted:#555;
  --line:#d6d6d6;
  --cream:#fdf3e2;
  --dark-btn:#333;
  --white:#fff;
}
*{box-sizing:border-box;margin:0;padding:0}
html,body{width:1200px;height:3066px;overflow:hidden;background:var(--white)}
body{font-family:"Inter",sans-serif;color:var(--ink);position:relative}
svg{display:block}

/* header */
.site-header{position:absolute;left:0;top:0;width:1200px;height:97px;border-bottom:1px solid #eee;background:#fff}
.brand{position:absolute;left:113px;top:32px;display:flex;align-items:center;gap:8px;font-size:26px;color:var(--ink)}
.brand-dot{width:20px;height:20px;border-radius:50%;background:var(--orange)}
.brand b{font-weight:700}
.nav{position:absolute;top:40px;left:305px;font-size:15px;color:#444}
.nav a{position:absolute;white-space:nowrap;text-decoration:none;color:#444}
.nav .active{color:var(--orange);font-weight:600}
.btn-header{position:absolute;left:958px;top:28px;width:130px;height:46px;border-radius:23px;background:var(--orange);color:#fff;font-weight:700;font-size:15px;display:flex;align-items:center;justify-content:center}

/* hero */
.hero{position:absolute;left:0;top:98px;width:1200px;height:516px;background:linear-gradient(180deg,#fff 0%,#fff 45%,var(--cream) 100%);overflow:hidden}
.hero-photo{position:absolute;left:800px;top:20px;width:400px;height:496px;border-radius:200px 0 0 40px;background:radial-gradient(circle at 50% 40%,#e9a64a 0%,#c77a28 55%,#f4dfc2 100%)}
.hero h1{position:absolute;left:110px;width:705px;top:88px;text-align:center;font-size:37px;font-weight:400;white-space:nowrap}
.hero h1 b{font-weight:700}
.hero p.lead{position:absolute;left:220px;width:485px;top:150px;text-align:center;font-size:20px;line-height:30px;color:#333}
.search{position:absolute;left:281px;top:236px;width:389px;height:60px;border:2px solid #ccc;border-radius:30px;background:#fff;display:flex;align-items:center;padding-left:38px;font-size:16px;color:#444}
.search-btn{position:absolute;right:22px;top:13px;width:34px;height:34px;border-radius:50%;background:var(--orange);display:flex;align-items:center;justify-content:center}
.chip{position:absolute;top:342px;height:47px;border:2px solid #ccc;border-radius:24px;display:flex;align-items:center;justify-content:center;gap:6px;font-size:16px;color:#333;background:#fff}
.chip.on{background:var(--orange);border-color:var(--orange);color:#fff}
.heart{position:absolute}

/* coupons */
.coupon{position:absolute;top:633px;width:219px;height:271px;border:2px solid var(--line);border-radius:6px;background:#fff;text-align:center}
.coupon.hot{background:var(--orange);border-color:var(--orange);color:#fff}
.coupon .store{margin-top:22px;display:flex;justify-content:center;align-items:center;gap:8px;font-size:15px}
.store-badge{width:32px;height:32px;border-radius:50%;border:3px solid var(--orange);background:#fff}
.coupon.hot .store-badge{border-color:#fff}
.coupon .deal{margin-top:14px;font-size:25px;font-weight:700;line-height:30px}
.coupon .deal small{display:block;font-size:18px;line-height:26px}
.coupon .fine{margin-top:12px;font-size:11px;color:#555}
.coupon.hot .fine{color:#fff}
.coupon .cta{margin:18px auto 0;height:40px;border-radius:20px;display:flex;align-items:center;justify-content:center;font-size:15px;font-weight:700;color:#fff;background:var(--dark-btn)}
.coupon.hot .cta{background:#fff;color:#444;font-weight:400}
.coupon .foot{position:absolute;bottom:22px;left:0;right:0;font-size:14px}

/* categories */
.tile{position:absolute;top:1073px;width:183px;height:147px;background:#fff;box-shadow:0 2px 8px rgba(0,0,0,.08);border-radius:4px;text-align:center}
.tile .ico{width:70px;height:70px;border-radius:50%;background:var(--orange);margin:18px auto 0;display:flex;align-items:center;justify-content:center}
.tile span{display:block;margin-top:22px;font-size:16px;color:#444}

/* product store */
.section-title{position:absolute;font-size:32px;font-weight:400;display:flex;align-items:center;gap:10px;white-space:nowrap}
.section-title b{font-weight:600}
.circle-arrow{position:absolute;width:34px;height:34px;border:2px solid #333;border-radius:50%;display:flex;align-items:center;justify-content:center}
.store-card{position:absolute;width:219px}
.store-card .photo{width:219px;height:230px}
.store-card .label{margin-top:20px;font-size:19px;display:flex;align-items:center;gap:8px}
.mini{width:20px;height:16px;border-radius:4px;background:var(--orange)}
.btn-pill{position:absolute;left:514px;top:1738px;width:201px;height:40px;border-radius:20px;background:var(--orange);color:#fff;font-size:15px;font-weight:600;display:flex;align-items:center;justify-content:center;gap:8px}

/* reviews */
.review{position:absolute;top:1972px;width:278px;height:193px;border:2px solid var(--line);border-radius:6px;background:#fff;padding:38px 18px 0 26px}
.review.lift{border-color:#fff;box-shadow:0 4px 16px rgba(0,0,0,.12)}
.quote-mark{position:absolute;left:10px;top:-17px;width:42px;height:42px;border-radius:50%;background:var(--orange);color:#fff;font-size:34px;font-weight:700;line-height:52px;text-align:center}
.review p{font-size:14px;line-height:23px;color:#333;height:46px}
.reviewer{display:flex;align-items:center;gap:16px;margin-top:16px}
.avatar{width:62px;height:62px;border-radius:50%;background:linear-gradient(135deg,#c9b3a4,#8a6a5a);flex:none}
.reviewer b{display:block;font-size:16px;font-weight:600;white-space:nowrap}
.stars{color:var(--orange);font-size:17px;letter-spacing:1px}

/* newsletter */
.join{position:absolute;left:0;top:2286px;width:1200px;height:400px;background:var(--orange);overflow:hidden}
.join-photo{position:absolute;left:622px;top:0;width:578px;height:400px;background:linear-gradient(90deg,var(--orange) 0%,#8a4a1a 18%,#5a3220 45%,#2e2420 75%,#b84a2a 100%)}
.join h2{position:absolute;left:113px;top:64px;width:520px;font-size:32px;line-height:44px;font-weight:500;color:#fff}
.join h2 .hl{display:inline-block}
.join p{position:absolute;left:114px;top:178px;width:470px;font-size:20px;line-height:31px;color:#fff}
.btn-white{position:absolute;left:113px;top:260px;width:244px;height:58px;border-radius:29px;background:#fff;color:#333;font-size:18px;display:flex;align-items:center;justify-content:center;gap:10px;letter-spacing:.5px}

/* footer */
.site-footer{position:absolute;left:0;top:2686px;width:1200px;height:380px}
.foot-brand{position:absolute;left:113px;top:90px;display:flex;align-items:center;gap:12px;font-size:32px}
.foot-brand b{font-weight:700}
.foot-about{position:absolute;left:114px;top:146px;width:260px;font-size:16px;line-height:25px;color:#444}
.socials{position:absolute;left:114px;top:266px;display:flex;gap:14px}
.socials span{width:28px;height:28px;border-radius:50%;background:#222}
.socials span.on{background:var(--orange)}
.col{position:absolute;top:94px}
.col h4{font-size:16px;font-weight:700;letter-spacing:.2px;margin-bottom:14px}
.col li{list-style:none;font-size:15px;color:#444;line-height:34.7px}
.legal{position:absolute;left:0;top:344px;width:1200px;border-top:1px solid #ddd;padding-top:15px;font-size:13px;color:#555;text-align:center}
</style>
</head>
<body>

<svg width="0" height="0" style="position:absolute">
  <defs>
    <symbol id="heart" viewBox="0 0 24 22"><path d="M12 21 C4 14 0 10 0 6 A6 6 0 0 1 12 4 A6 6 0 0 1 24 6 C24 10 20 14 12 21Z"/></symbol>
  </defs>
</svg>

<header class="site-header">
  <div class="brand"><span class="brand-dot"></span><span>Snout<b>Saver</b></span></div>
  <nav class="nav">
    <a class="active" style="left:0">Home</a>
    <a style="left:85px">Categories ▾</a>
    <a style="left:218px">Popular stores</a>
    <a style="left:364px">Latest deals</a>
    <a style="left:489px"><svg width="14" height="13" fill="#f6a623" style="display:inline;vertical-align:-1px"><use href="#heart"/></svg>&nbsp; My Favourites</a>
  </nav>
  <div class="btn-header">GET DEAL</div>
</header>

<section class="hero">
  <div class="hero-photo" role="img" aria-label="Happy golden retriever lying down, mouth open"></div>
  <svg class="heart" style="left:625px;top:50px" width="38" height="35" fill="#f6a623"><use href="#heart"/></svg>
  <svg class="heart" style="left:786px;top:50px" width="24" height="22" fill="#f6a623"><use href="#heart"/></svg>
  <svg class="heart" style="left:747px;top:178px" width="40" height="37" fill="#f6a623"><use href="#heart"/></svg>
  <svg class="heart" style="left:237px;top:208px" width="22" height="20" fill="#f6a623"><use href="#heart"/></svg>
  <svg class="heart" style="left:194px;top:256px" width="38" height="35" fill="#f6a623"><use href="#heart"/></svg>
  <svg class="heart" style="left:1125px;top:35px" width="40" height="37" fill="#f6a623"><use href="#heart"/></svg>

  <h1>Save on Everything <b>your Dog Loves</b></h1>
  <p class="lead">Verified deals updated daily — because your pup deserves the best for less.</p>
  <div class="search">Search for treats, toys, or stores...
    <span class="search-btn"><svg width="16" height="16" fill="none" stroke="#fff" stroke-width="2.4"><circle cx="7" cy="7" r="5"/><path d="M11 11l4 4"/></svg></span>
  </div>
  <div class="chip on" style="left:140px;width:98px">Food</div>
  <div class="chip" style="left:266px;width:98px">Toys</div>
  <div class="chip" style="left:386px;width:120px">Health</div>
  <div class="chip" style="left:524px;width:125px">Services</div>
  <div class="chip" style="left:662px;width:124px">Outdoor</div>
</section>

<div class="coupon hot" style="left:114px">
  <div class="store"><span class="store-badge"></span>Sunny Snout</div>
  <div class="deal">25% OFF<small>Dog Treats!</small></div>
  <div class="fine">Get 25% off on your first order.</div>
  <div class="cta" style="width:132px">COPY CODE</div>
  <div class="foot">Get Deal</div>
</div>
<div class="coupon" style="left:367px">
  <div class="store"><span class="store-badge"></span>Green Kennel</div>
  <div class="deal"><small style="font-size:21px">Buy 1 Get 1 Free</small>Toys!</div>
  <div class="fine">Free toy with every order.</div>
  <div class="cta" style="width:152px">COPIED</div>
  <div class="foot">Expires in 3 days</div>
</div>
<div class="coupon" style="left:619px">
  <div class="store"><span class="store-badge"></span>WagTrail</div>
  <div class="deal">$10 OFF<small>Select Dog good</small></div>
  <div class="fine">Save $10 on selected dog food.</div>
  <div class="cta" style="width:132px">GET DEAL</div>
  <div class="foot">Get Deal</div>
</div>
<div class="coupon" style="left:872px">
  <div class="store"><span class="store-badge"></span>FurWell</div>
  <div class="deal">20% OFF<small style="font-size:17px">Grooming Services</small></div>
  <div class="fine">Enjoy 20% off any grooming service.</div>
  <div class="cta" style="width:132px">COPY CODE</div>
  <div class="foot">Get Deal</div>
</div>

<svg class="heart" style="left:294px;top:1026px" width="30" height="28" fill="#f6a623"><use href="#heart"/></svg>
<svg class="heart" style="left:540px;top:1028px" width="27" height="25" fill="#f6a623"><use href="#heart"/></svg>
<svg class="heart" style="left:929px;top:1013px" width="36" height="33" fill="#f6a623"><use href="#heart"/></svg>
<svg class="heart" style="left:48px;top:1130px" width="37" height="34" fill="#f6a623"><use href="#heart"/></svg>

<div class="tile" style="left:113px"><div class="ico"><svg width="34" height="26" fill="#fff"><rect x="3" y="8" width="28" height="16" rx="3"/><rect x="8" y="2" width="18" height="6" rx="2"/></svg></div><span>Toys &amp; Accessories</span></div>
<div class="tile" style="left:312px"><div class="ico"><svg width="30" height="30" fill="#fff"><circle cx="12" cy="8" r="6"/><rect x="8" y="14" width="16" height="14" rx="3"/></svg></div><span>Training &amp; Services</span></div>
<div class="tile" style="left:510px"><div class="ico"><svg width="30" height="32" fill="#fff"><circle cx="10" cy="10" r="8"/><rect x="8" y="16" width="4" height="14"/><rect x="15" y="20" width="14" height="4"/><rect x="15" y="26" width="14" height="4"/></svg></div><span>Outdoor &amp; Travel</span></div>
<div class="tile" style="left:709px"><div class="ico"><svg width="32" height="30" fill="#fff"><circle cx="16" cy="18" r="8"/><circle cx="6" cy="10" r="4"/><circle cx="26" cy="10" r="4"/><circle cx="12" cy="4" r="3.5"/><circle cx="20" cy="4" r="3.5"/></svg></div><span>Vet &amp; Insurance</span></div>
<div class="tile" style="left:907px"><div class="ico"><svg width="34" height="28" fill="#fff"><path d="M2 14h30a15 12 0 0 1-30 0z"/><rect x="12" y="2" width="10" height="10" rx="3"/></svg></div><span>Food &amp; Treats</span></div>

<h2 class="section-title" style="left:113px;top:1355px"><span class="mini" style="width:32px;height:28px"></span>Our Product <b>Store</b></h2>
<div class="circle-arrow" style="left:1009px;top:1363px"><svg width="16" height="14" fill="none" stroke="#333" stroke-width="2"><path d="M15 7H2M7 2L2 7l5 5"/></svg></div>
<div class="circle-arrow" style="left:1054px;top:1363px"><svg width="16" height="14" fill="none" stroke="#333" stroke-width="2"><path d="M1 7h13M9 2l5 5-5 5"/></svg></div>

<div class="store-card" style="left:113px;top:1430px"><div class="photo" role="img" aria-label="Shelf of dog food bags in a pet store" style="background:linear-gradient(160deg,#2c3f78,#c89a55 50%,#1f2d5c)"></div><div class="label"><span class="mini"></span>Food</div></div>
<div class="store-card" style="left:366px;top:1430px"><div class="photo" role="img" aria-label="Vet with a small tan dog at a clinic" style="background:linear-gradient(160deg,#e7e7ec,#c08a5a 55%,#2b3e5a)"></div><div class="label" style="margin-top:16px"><span class="mini"></span>Health</div></div>
<div class="store-card" style="left:619px;top:1430px"><div class="photo" role="img" aria-label="Puppy lying beside plush toys" style="background:linear-gradient(160deg,#e8e4de,#d7c7b0 55%,#b9a48a)"></div><div class="label" style="margin-top:14px"><span class="mini"></span>Toy</div></div>
<div class="store-card" style="left:872px;top:1422px"><div class="photo" role="img" aria-label="Husky on a leash sitting on grass during training" style="background:linear-gradient(160deg,#4a5a3a,#6aa048 55%,#3d7a2c)"></div><div class="label" style="margin-top:18px"><span class="mini"></span>Training &amp; Services</div></div>

<div class="btn-pill">VIEW ALL STORES <svg width="14" height="12" fill="none" stroke="#fff" stroke-width="2"><path d="M0 6h12M7 1l5 5-5 5"/></svg></div>

<h2 class="section-title" style="left:322px;top:1884px"><span class="brand-dot" style="width:28px;height:28px"></span>Why Dog Lovers <b>Trust SnoutSaver</b></h2>
<svg class="heart" style="left:924px;top:1907px" width="34" height="31" fill="#fce3bd"><use href="#heart"/></svg>
<svg class="heart" style="left:580px;top:1942px" width="22" height="20" fill="#fce3bd"><use href="#heart"/></svg>

<div class="circle-arrow" style="left:77px;top:2042px;width:38px;height:38px"><svg width="16" height="14" fill="none" stroke="#333" stroke-width="2"><path d="M15 7H2M7 2L2 7l5 5"/></svg></div>
<div class="circle-arrow" style="left:1088px;top:2042px;width:38px;height:38px"><svg width="16" height="14" fill="none" stroke="#333" stroke-width="2"><path d="M1 7h13M9 2l5 5-5 5"/></svg></div>

<div class="review" style="left:141px">
  <span class="quote-mark">“</span>
  <p>“I save $30 a month on food for Biscuit—thank you SnoutSaver!”</p>
  <div class="reviewer"><span class="avatar" role="img" aria-label="Reviewer portrait"></span><div><b>Maya , Boulder CO</b><span class="stars">★★★★★</span></div></div>
</div>
<div class="review lift" style="left:463px">
  <span class="quote-mark">“</span>
  <p>“I used SnoutSaver to get 30% off our first bag of premium kibble.</p>
  <div class="reviewer"><span class="avatar" role="img" aria-label="Reviewer portrait"></span><div><b>Sam R.,Austin TX</b><span class="stars">★★★★★</span></div></div>
</div>
<div class="review" style="left:781px">
  <span class="quote-mark">“</span>
  <p>“Finally a coupon site that actually works! Got a killer deal</p>
  <div class="reviewer"><span class="avatar" role="img" aria-label="Reviewer portrait"></span><div><b>Parker, Olivia</b><span class="stars">★★★★★</span></div></div>
</div>

<section class="join">
  <div class="join-photo" role="img" aria-label="Three puppies peeking out of a red shopping bag with warm bokeh lights"></div>
  <svg class="heart" style="left:590px;top:22px" width="26" height="24" fill="#fff"><use href="#heart"/></svg>
  <svg class="heart" style="left:590px;top:142px" width="26" height="24" fill="#fff"><use href="#heart"/></svg>
  <svg class="heart" style="left:48px;top:196px" width="24" height="22" fill="#fff"><use href="#heart"/></svg>
  <svg class="heart" style="left:418px;top:248px" width="30" height="28" fill="#fff"><use href="#heart"/></svg>
  <svg class="heart" style="left:455px;top:320px" width="18" height="16" fill="#fff"><use href="#heart"/></svg>
  <svg class="heart" style="left:230px;top:370px" width="28" height="25" fill="#fff"><use href="#heart"/></svg>
  <h2><span class="hl">Join Our Pack – Get Tail-Wagging</span> Deals in Your Inbox! <svg width="18" height="16" fill="#fff" style="display:inline"><use href="#heart"/></svg></h2>
  <p>Be the first to fetch exclusive discounts, new deals, and hand-picked treats for your pup.</p>
  <div class="btn-white">VIEW ALL DEALS <svg width="18" height="14" fill="none" stroke="#333" stroke-width="2"><path d="M0 7h16M10 1l6 6-6 6"/></svg></div>
</section>

<footer class="site-footer">
  <div class="foot-brand"><span class="brand-dot" style="width:30px;height:30px"></span><span>Snout<b>Saver</b></span></div>
  <p class="foot-about">Save on everything your dog loves. Verified coupons, trusted brands, and deals updated daily for dog lovers everywhere.</p>
  <div class="socials"><span></span><span></span><span class="on"></span><span></span></div>
  <div class="col" style="left:423px"><h4>EXPLORE CATEGORIES</h4><ul><li>Dog Food &amp; Treats</li><li>Toys &amp; Accessories</li><li>Health &amp; Grooming</li><li>Training &amp; Services</li><li>Outdoor &amp; Travel</li></ul></div>
  <div class="col" style="left:688px"><h4>POPULAR STORES</h4><ul><li>Munchly Deals</li><li>WoofCrate Offers</li><li>PetNook Discounts</li><li>Riverway Pets</li><li>The Kibble Kitchen</li></ul></div>
  <div class="col" style="left:949px"><h4>COMPANY INFO</h4><ul><li>About Us</li><li>Contact</li><li>Privacy Policy</li><li>Terms of Service</li><li>Submit a Deal</li></ul></div>
  <div class="legal">© 2025 SnoutSaver. All rights reserved. &nbsp; SnoutSaver™ is a registered trademark. All brand names are the property of their respective owners.</div>
</footer>

</body>
</html>
```